Business cards

I would like a black background with the design I previously chose. I need 2 sets of cards. Mine will have Marlene Ridgeway, Broker/Owner, 307-481-7263 and marlene.brightharbor@quillpost.example
The second set will read, Corey Albrecht, Realtor 307-538-2409, corey.brightharbor@quillpost.example

```html
<!DOCTYPE html>
<html lang="en">
<head>
<meta charset="utf-8">
<title>Bright Harbor – Business Cards</title>
<link href="https://fonts.googleapis.com/css2?family=Roboto:wght@400;500&family=Roboto+Condensed:wght@700&display=swap" rel="stylesheet">
<style>
  :root {
    --stage: #1a1a1b;
    --card: #222325;
    --silver: #bfbfbf;
    --silver-dim: #8a8a8a;
    --ink-light: #ececec;
    --divider: #6a6a6a;
  }
  * { margin: 0; padding: 0; box-sizing: border-box; }
  html, body {
    width: 1200px; height: 960px; overflow: hidden;
    background: var(--stage);
    font-family: "Roboto", Arial, sans-serif;
  }
  .canvas { position: relative; width: 1200px; height: 960px; }
  .card {
    position: absolute; width: 600px; height: 342px;
    background: var(--card);
  }
  .card--front { left: 313px; top: 113px; }
  .card--back { left: 311px; top: 473px; }

  .brand { position: absolute; text-align: center; }
  .brand__mark {
    display: block; margin: 0 auto;
    border-radius: 50%;
    border: 3px solid var(--silver-dim);
  }
  .brand__name {
    display: block; color: var(--silver);
    font-family: "Roboto", Arial, sans-serif; font-weight: 500;
    letter-spacing: 1px; white-space: nowrap;
  }
  .card--front .brand { left: 55px; top: 105px; width: 200px; }
  .card--front .brand__mark { width: 80px; height: 80px; }
  .card--front .brand__name { font-size: 21px; margin-top: 14px; }
  .card--back .brand { left: 150px; top: 82px; width: 300px; }
  .card--back .brand__mark { width: 110px; height: 110px; }
  .card--back .brand__name { font-size: 29px; margin-top: 16px; }

  .divider {
    position: absolute; left: 285px; top: 102px;
    width: 1px; height: 135px; background: var(--divider);
  }
  .person { position: absolute; left: 310px; top: 112px; }
  .person__name {
    font-family: "Roboto Condensed", Arial, sans-serif; font-weight: 700;
    font-size: 21px; color: var(--silver); letter-spacing: 0.2px;
  }
  .person__role {
    font-size: 15px; font-weight: 500; color: var(--ink-light);
    margin-top: 3px; letter-spacing: 0.3px;
  }
  .contact { list-style: none; margin-top: 19px; }
  .contact__item {
    display: flex; align-items: center; gap: 8px;
    font-size: 14px; color: var(--ink-light); height: 19.5px;
  }
  .contact__icon { width: 14px; height: 14px; flex: none; fill: var(--silver); }

  .web {
    position: absolute; left: 0; right: 0; top: 286px;
    text-align: center; font-size: 15px; color: var(--ink-light);
    letter-spacing: 4px;
  }
</style>
</head>
<body>
<main class="canvas">
  <section class="card card--front">
    <div class="brand">
      <span class="brand__mark"></span>
      <span class="brand__name">BRIGHT HARBOR</span>
    </div>
    <div class="divider"></div>
    <div class="person">
      <p class="person__name">MARLENE RIDGEWAY</p>
      <p class="person__role">BROKER/OWNER</p>
      <ul class="contact">
        <li class="contact__item">
          <svg class="contact__icon" viewBox="0 0 14 14" aria-hidden="true"><path d="M3.5 0h7a1 1 0 0 1 1 1v12a1 1 0 0 1-1 1h-7a1 1 0 0 1-1-1V1a1 1 0 0 1 1-1zm.6 1.8v9h5.8v-9zM7 11.6a.8.8 0 1 0 0 1.6.8.8 0 0 0 0-1.6z"/></svg>
          307-481-7263
        </li>
        <li class="contact__item">
          <svg class="contact__icon" viewBox="0 0 14 14" aria-hidden="true"><path d="M1 3.5h12v7H1zM1.6 4l5.4 3.6L12.4 4v.9L7 8.5 1.6 4.9z" fill-rule="evenodd"/></svg>
          marlene.brightharbor@quillpost.example
        </li>
        <li class="contact__item">
          <svg class="contact__icon" viewBox="0 0 14 14" aria-hidden="true"><circle cx="7" cy="7" r="6"/><path d="M4 4.5c1 .2 1.5 1 2.3 1.2.6.2.4 1.4-.3 1.6-.8.2-.5 1.5-1.2 2C4 9.6 3 8 3 7s.3-2 1-2.5zM8.5 3c.8.4 1.5 1.3 1 2-.4.6-1.3.3-1.6-.4C7.6 4 7.8 3.2 8.5 3zm1.3 4.5c.6.4.8 1.5.2 2.3-.6.7-1.6.5-1.6-.4 0-.9.8-2.2 1.4-1.9z" fill="#222325"/></svg>
          www.brightharbor.example
        </li>
      </ul>
    </div>
  </section>

  <section class="card card--back">
    <div class="brand">
      <span class="brand__mark"></span>
      <span class="brand__name">BRIGHT HARBOR</span>
    </div>
    <p class="web">www.brightharbor.example</p>
  </section>
</main>
</body>
</html>
```